Business Cards for company that supports physicians that do medical research

Need to create a business card for Qorvel Studies (www.qorvelstudies.example), a company devoted to supporting physicians who conduct medical research. The form of the card should match the message of research and information quest. I have provided the logo of the company as an uploaded file. Designs should be simple and slick aimed at very high end clients.

Target Market(s)

Medical doctors that are also researchers

Industry/Entity Type

Medical

Contact Information for Business Card

Should feature logo and fields for personal info:
Name/title
Phone /email

Font styles to use
Serif
Sans Serif

Requirements
Must have
• Qorvel logo and fields for personal info:
• Name: Bertrand Okonfu
• Title: VP Research and Senior Analyst
• Phone: 555-203-4719
• email: info@qorvelstudies.example
Nice to have
• Interesting cards that I've seen:
• 1- all black/charcoal or very dark background
• 2- Plastic - semi-transparent
• 3- non-standard height-width ratios
• 4- Functional cards -- USB drive incorporated
Should not have
• Too busy; needs to stay very simple

```html
<!DOCTYPE html>
<html lang="en">
<head>
<meta charset="utf-8">
<title>Qorvel Studies – Business Card</title>
<link href="https://fonts.googleapis.com/css2?family=Open+Sans:ital,wght@0,400;0,600;1,400&display=swap" rel="stylesheet">
<style>
  :root {
    --backdrop: #3a3a3a;
    --card-blue: #1d7dc0;
    --card-green: #49b142;
    --paper-white: #ffffff;
    --brand-blue: #1d7dc0;
    --text-white: #ffffff;
  }
  * { margin: 0; padding: 0; box-sizing: border-box; }
  html, body {
    width: 1200px;
    height: 750px;
    overflow: hidden;
    background: var(--backdrop);
    font-family: "Open Sans", sans-serif;
  }
  .canvas {
    position: relative;
    width: 1200px;
    height: 750px;
  }
  .card {
    position: absolute;
    top: 228px;
    width: 461px;
    height: 262px;
    overflow: hidden;
  }
  .card--front { left: 124px; background: var(--card-blue); }
  .card--back { left: 618px; background: var(--card-green); }

  .front-swoosh {
    position: absolute;
    inset: 0;
    width: 461px;
    height: 262px;
  }
  .front-brand {
    position: absolute;
    left: 46px;
    top: 88px;
    font-size: 27px;
    font-weight: 600;
    color: var(--brand-blue);
    letter-spacing: 0.5px;
  }
  .holder {
    position: absolute;
    right: 22px;
    top: 146px;
    text-align: right;
    color: var(--text-white);
  }
  .holder__name { font-size: 16px; font-weight: 600; line-height: 20px; }
  .holder__title { font-size: 12.5px; line-height: 18px; }

  .contact-list {
    position: absolute;
    right: 24px;
    top: 197px;
    list-style: none;
    color: var(--text-white);
    font-size: 11.5px;
  }
  .contact-list li {
    display: flex;
    justify-content: flex-end;
    align-items: center;
    gap: 7px;
    height: 17.5px;
  }
  .contact-list svg { width: 12px; height: 12px; flex: none; }

  .back-brand {
    position: absolute;
    left: 0;
    right: 0;
    top: 104px;
    text-align: center;
    font-size: 30px;
    font-weight: 600;
    color: var(--text-white);
    letter-spacing: 0.5px;
  }
  .back-web {
    position: absolute;
    left: 0;
    right: 0;
    top: 216px;
    text-align: center;
    font-size: 11px;
    font-style: italic;
    letter-spacing: 3px;
    color: var(--text-white);
  }
</style>
</head>
<body>
<main class="canvas">

  <section class="card card--front" aria-label="Business card front">
    <svg class="front-swoosh" viewBox="0 0 461 262" aria-hidden="true">
      <path d="M0,36 C60,18 130,12 190,16 C280,24 318,70 298,114 C262,188 120,248 0,262 Z" fill="var(--paper-white)"/>
    </svg>
    <div class="front-brand">Qorvel Studies</div>

    <div class="holder">
      <p class="holder__name">Bertrand Okonfu</p>
      <p class="holder__title">VP Research &amp; Senior Analyst</p>
    </div>

    <ul class="contact-list">
      <li>555-203-4719
        <svg viewBox="0 0 24 24" aria-hidden="true"><path fill="#fff" d="M6.6 10.8a15.1 15.1 0 0 0 6.6 6.6l2.2-2.2c.3-.3.7-.4 1-.2 1.1.4 2.3.6 3.6.6.6 0 1 .4 1 1V20c0 .6-.4 1-1 1A17 17 0 0 1 3 4c0-.6.4-1 1-1h3.5c.6 0 1 .4 1 1 0 1.3.2 2.5.6 3.6.1.3 0 .7-.2 1z"/></svg>
      </li>
      <li>info@qorvelstudies.example
        <svg viewBox="0 0 24 24" aria-hidden="true"><rect x="2" y="5" width="20" height="14" fill="#fff"/><path d="M2 5l10 8 10-8" fill="none" stroke="var(--card-blue)" stroke-width="1.8"/></svg>
      </li>
      <li>www.qorvelstudies.example
        <svg viewBox="0 0 24 24" aria-hidden="true"><circle cx="12" cy="12" r="10" fill="#fff"/><path d="M12 2v20M2 12h20M12 2c-4 4-4 16 0 20M12 2c4 4 4 16 0 20" fill="none" stroke="var(--card-blue)" stroke-width="1.4"/></svg>
      </li>
    </ul>
  </section>

  <section class="card card--back" aria-label="Business card back">
    <div class="back-brand">Qorvel Studies</div>
    <p class="back-web">www.qorvelstudies.example</p>
  </section>

</main>
</body>
</html>
```